QHX Compliant Dietary Supplement Label for Nutritional Company

We are in need of a label for our line of 20+ dietary supplements that are specifically formulated to balance body chemistry and match the biochemical individuality of our users based on hair tissue mineral analysis.

We have a line of approximately 20 different dietary supplements that will require use of new label in both a small (90 capsule) and large (180 capsule) size. We will start with the initial label in which Product name, Supplement Facts, and Ingredient list will need to be modified for each particular product thereafter.

The label will be placed on a transparent blue bottle with the color of lid being decided after label design. We are open to a transparent light amber bottle with black lid but blue is our preference.

We would like the majority of the label to be blue. Solid blue, fading of blue to darker blue/black, or subtle background designs are welcome with involvement of white and hints of orange. We do not want pictorial images on the label.

Label size:
Small bottle (120cc): Label size ~ 2.25” x 5.875”
Large bottle (200cc): Label size ~ 2.75” x 7.625”

Front:
-Logo near top of label with product name and description in middle and capsule count near the bottom

Right Side:
-Supplement Facts: See current product image below in brief
-Ingredient list: See current product image below in brief
-Manufactured for: See image below (This is on the left side of our current bottle and would like it moved to the bottom of the right side)

Left side:
-Suggested use: See current product image below in brief
-Leave room for possible warning statement
-Leave room for possible lot number printing
-Keep out of the reach of children.

The first files below are our current supplement label with product information. This information is what is needed on the label and will likely need some adjustments as we are updating our line of supplements and changes in QHX requirements.

The following files are the logo files and color palette.

The remaining files are some designs we came across for inspiration.

Thank you.

Target Market(s)

Health Care Profressionals

Industry/Entity Type

Health Care and Nutrition

Requirements
Nice to have
• Product name needs to be on same line in all one color
Should not have
• Pictorial Images

```html
<!DOCTYPE html>
<html lang="en">
<head>
<meta charset="utf-8">
<title>ADRAVIN Adrenal Supplement – Label Panels</title>
<link rel="stylesheet" href="https://fonts.googleapis.com/css2?family=Oswald:wght@500;600;700&family=Jost:wght@300;400;500;600&family=Roboto+Condensed:wght@400;700&display=swap">
<style>
  :root {
    --stage: #cfcccc;
    --navy-deep: #0b1636;
    --navy: #1b2c57;
    --orange: #e88a3a;
    --orange-light: #f0a055;
    --sky: #7198cf;
    --sky-light: #86a9d8;
    --strip: #101a3c;
    --white: #ffffff;
    --ink: #10162e;
    --rule: #1d2a55;
    --brand-blue: #4c7cc4;
  }
  * { box-sizing: border-box; margin: 0; padding: 0; }
  html, body { width: 1200px; height: 829px; overflow: hidden; }
  body {
    background: var(--stage);
    font-family: "Jost", sans-serif;
    position: relative;
  }
  .label-set {
    position: absolute;
    left: 36px; top: 114px;
    display: flex; gap: 24px;
  }
  .panel {
    width: 360px; height: 600px;
    display: flex; flex-direction: column;
    overflow: hidden;
    border-radius: 6px;
  }
  .panel-body {
    height: 382px;
    background: linear-gradient(160deg, var(--navy-deep) 0%, var(--navy) 55%, var(--navy-deep) 100%);
    position: relative;
  }
  .band {
    height: 56px;
    background: linear-gradient(90deg, var(--orange) 0%, var(--orange-light) 50%, var(--orange) 100%);
    display: flex; align-items: center;
    font-family: "Oswald", sans-serif; font-weight: 600;
    font-size: 30px; letter-spacing: 2px; color: var(--ink);
    text-transform: uppercase;
  }
  .field {
    height: 140px;
    background: linear-gradient(180deg, var(--sky) 0%, var(--sky-light) 100%);
  }
  .foot { height: 22px; background: var(--strip); }

  /* Left side */
  .info { padding: 34px 28px 0; color: var(--white); }
  .info-title {
    color: var(--orange); font-weight: 600; font-size: 21px;
    letter-spacing: .5px; margin-bottom: 10px;
  }
  .info-title + p { font-size: 17.5px; font-weight: 300; line-height: 1.35; }
  .info-block { margin-bottom: 30px; }
  .company { font-weight: 600; }
  .info-title + p.notice-text { font-weight: 500; }
  .band-expiry { padding-left: 28px; }

  /* Front */
  .brand {
    position: absolute; left: 28px; top: 56px;
    display: flex; align-items: center; gap: 10px;
    color: var(--brand-blue); font-weight: 400; font-size: 20px;
    letter-spacing: 3px; line-height: 1.1;
  }
  .brand-dot { width: 14px; height: 14px; border-radius: 50%; background: var(--orange); flex: none; }
  .product-name {
    position: absolute; left: 0; right: 0; bottom: 14px;
    text-align: center;
    font-family: "Oswald", sans-serif; font-weight: 700;
    font-size: 84px; line-height: 1; letter-spacing: 0;
    color: var(--white); white-space: nowrap;
  }
  .band-centered { justify-content: center; }
  .count-field { display: flex; flex-direction: column; align-items: center; padding-top: 8px; }
  .count {
    font-family: "Oswald", sans-serif; font-weight: 700;
    font-size: 74px; line-height: 1; color: var(--navy-deep);
  }
  .count-unit {
    font-weight: 600; font-size: 17px; letter-spacing: 6px;
    color: var(--white); margin-top: 6px;
  }

  /* Right side */
  .facts {
    position: absolute; left: 14px; top: 18px;
    width: 332px;
    background: var(--white); color: var(--ink);
    padding: 10px 12px 10px;
    font-family: "Roboto Condensed", sans-serif;
  }
  .facts-title { font-family: "Jost", sans-serif; font-weight: 600; font-size: 23px; letter-spacing: .5px; line-height: 1.05; }
  .facts-serving { font-family: "Jost", sans-serif; font-weight: 500; font-size: 11px; line-height: 1.25; margin-top: 4px; }
  .facts-table { width: 100%; border-collapse: collapse; margin-top: 6px; border-top: 3px solid var(--rule); font-size: 8.5px; }
  .facts-table th { font-weight: 700; font-size: 9px; text-align: right; line-height: 1.1; padding: 4px 0 3px 6px; border-bottom: 1.5px solid var(--rule); }
  .facts-table td { padding: 3px 0 2px; border-bottom: 1px solid var(--rule); }
  .facts-table td.amt, .facts-table td.dv { text-align: right; padding-left: 6px; white-space: nowrap; }
  .facts-table tr.section-end td { border-bottom: 2.5px solid var(--rule); }
  .facts-table tr.last td { border-bottom: 3px solid var(--rule); }
  .facts-note { font-size: 8.5px; margin-top: 8px; }
  .ingredients {
    display: flex; align-items: center; justify-content: center;
    text-align: center; color: var(--navy-deep);
    font-size: 18px; line-height: 1.55; font-weight: 400;
  }
</style>
</head>
<body>
<main class="label-set">

  <section class="panel panel-left">
    <div class="panel-body info">
      <div class="info-block">
        <h2 class="info-title">DISTRIBUTED BY:</h2>
        <p><span class="company">NORVEN LABORATORIES, INC.</span><br>Ridgeview, AZ 85090 USA</p>
      </div>
      <div class="info-block">
        <h2 class="info-title">SUGGESTED USE:</h2>
        <p>One capsule daily or as directed by<br>a physician.</p>
      </div>
      <div class="info-block">
        <h2 class="info-title">NOTICE:</h2>
        <p class="notice-text">Keep out of the reach of children.</p>
      </div>
    </div>
    <div class="band band-expiry">Date of Expiry :</div>
    <div class="field"></div>
    <div class="foot"></div>
  </section>

  <section class="panel panel-front">
    <div class="panel-body">
      <div class="brand">
        <span class="brand-dot"></span>
        <span>NORVEN<br>LABORATORIES</span>
      </div>
      <h1 class="product-name">ADRAVIN</h1>
    </div>
    <div class="band band-centered">Adrenal Supplement</div>
    <div class="field count-field">
      <span class="count">180</span>
      <span class="count-unit">CAPSULES</span>
    </div>
    <div class="foot"></div>
  </section>

  <section class="panel panel-right">
    <div class="panel-body">
      <div class="facts">
        <h2 class="facts-title">SUPPEMENT FACTS</h2>
        <p class="facts-serving">Serving Size: 1 Capsule<br>Servings Per Container: 90</p>
        <table class="facts-table">
          <thead>
            <tr><th></th><th>Amount Per<br>Serving</th><th>% Daily<br>Value</th></tr>
          </thead>
          <tbody>
            <tr><td>Vitamin C (as ascorbic acid)</td><td class="amt">100 mg</td><td class="dv">111%</td></tr>
            <tr><td>Vitamin B5 (as D-calcium pantothenate)</td><td class="amt">100 mg</td><td class="dv">2000%</td></tr>
            <tr><td>Magnesium (as magnesium amino acid chelate)</td><td class="amt">5 mg</td><td class="dv">1%</td></tr>
            <tr><td>Zinc (as zinc amino acid chelate)</td><td class="amt">1 mg</td><td class="dv">9%</td></tr>
            <tr><td>Manganese (as manganese amino acid chelate)</td><td class="amt">1 mg</td><td class="dv">43%</td></tr>
            <tr class="section-end"><td>Potassium (as potassium amino acid chelate)</td><td class="amt">25 mg</td><td class="dv">1%</td></tr>
            <tr><td>Suprarenal (adrenal) powder (bovine)</td><td class="amt">100 mg</td><td class="dv">†</td></tr>
            <tr><td>Liver powder, defatted (bovine)</td><td class="amt">45 mg</td><td class="dv">†</td></tr>
            <tr class="last"><td>Betaine Hydrochloride</td><td class="amt">25 mg</td><td class="dv">†</td></tr>
          </tbody>
        </table>
        <p class="facts-note">Daily Value not established</p>
      </div>
    </div>
    <div class="band band-centered">Other Ingredients:</div>
    <div class="field ingredients">
      <p>Hypromellose<br>(Vegetable Capsule),<br>RiceFlo (Organic Rice Fiber)</p>
    </div>
    <div class="foot"></div>
  </section>

</main>
</body>
</html>
```